Business Card Design Project for Heron Lending

Hello there,

We are looking for a business card design for our new Heron Lending car financing company. We are looking for a business card that will include:

- An address
- Telephone number and extension
- Employee Name
- Employee Title
- Our logo and name clearly visible

We are including our logo with this writeup, we are looking to convey friendliness, trus and memorability. Colors and everything else is up to you.

Target Market(s)

18-34 year old males and females

Industry/Entity Type

Business

```html
<!DOCTYPE html>
<html lang="en">
<head>
<meta charset="utf-8">
<title>Heron Lending – Business Card</title>
<link rel="stylesheet" href="https://fonts.googleapis.com/css2?family=Open+Sans:wght@400;600;700&display=swap">
<style>
  :root {
    --backdrop: #e9e9e8;
    --card-white: #fbfbfb;
    --card-stone: #eeeeeb;
    --navy: #173c52;
    --ink: #1d1d1d;
    --text-grey: #3a3a3a;
  }
  * { box-sizing: border-box; margin: 0; padding: 0; }
  html, body {
    width: 1200px;
    height: 675px;
    overflow: hidden;
    background: var(--backdrop);
    font-family: "Open Sans", Arial, sans-serif;
  }
  .canvas {
    position: relative;
    width: 1200px;
    height: 675px;
  }
  .card {
    position: absolute;
    top: 189px;
    width: 520px;
    height: 297px;
    overflow: hidden;
    box-shadow: 0 6px 18px rgba(0, 0, 0, 0.12);
  }
  .card--front {
    left: 50px;
    background: var(--card-white);
    display: flex;
    align-items: center;
    justify-content: center;
  }
  .card--back {
    left: 630px;
    background: var(--card-stone);
  }
  .brand {
    display: flex;
    align-items: center;
    gap: 10px;
    color: var(--navy);
    font-weight: 700;
    letter-spacing: 0.04em;
    text-transform: uppercase;
  }
  .brand__dot {
    border-radius: 50%;
    background: var(--navy);
  }
  .card--front .brand { font-size: 34px; }
  .card--front .brand__dot { width: 26px; height: 26px; }
  .card--back .brand {
    position: absolute;
    left: 52px;
    top: 118px;
    font-size: 20px;
  }
  .card--back .brand__dot { width: 16px; height: 16px; }
  .holder {
    position: absolute;
    right: 26px;
    top: 22px;
    text-align: right;
    color: var(--navy);
  }
  .holder__name { font-size: 17px; font-weight: 700; line-height: 1.2; }
  .holder__title { font-size: 12px; font-weight: 400; }
  .contact {
    position: absolute;
    left: 28px;
    top: 190px;
    list-style: none;
    color: var(--text-grey);
    font-size: 12.5px;
    line-height: 1.55;
  }
  .contact li { display: flex; align-items: center; gap: 7px; }
  .contact svg { width: 11px; height: 11px; fill: var(--ink); flex: none; }
  .bands {
    position: absolute;
    left: 0;
    bottom: 0;
    width: 520px;
    height: 297px;
    pointer-events: none;
  }
  .bands__navy { fill: var(--navy); }
  .bands__ink { fill: var(--ink); }
</style>
</head>
<body>
<main class="canvas">
  <section class="card card--front" aria-label="Card front">
    <div class="brand"><span class="brand__dot"></span>Heron Lending</div>
  </section>

  <section class="card card--back" aria-label="Card back">
    <div class="holder">
      <p class="holder__name">Your Long Name</p>
      <p class="holder__title">Your Title</p>
    </div>

    <div class="brand"><span class="brand__dot"></span>Heron Lending</div>

    <ul class="contact">
      <li>
        <svg viewBox="0 0 24 24" aria-hidden="true"><path d="M6.6 10.8a15 15 0 0 0 6.6 6.6l2.2-2.2a1 1 0 0 1 1-.25 11.4 11.4 0 0 0 3.6.57 1 1 0 0 1 1 1V20a1 1 0 0 1-1 1A17 17 0 0 1 3 4a1 1 0 0 1 1-1h3.5a1 1 0 0 1 1 1c0 1.25.2 2.45.57 3.57a1 1 0 0 1-.25 1z"/></svg>
        00.00.00.0000
      </li>
      <li>
        <svg viewBox="0 0 24 24" aria-hidden="true"><path d="M12 2a7 7 0 0 0-7 7c0 5.2 7 13 7 13s7-7.8 7-13a7 7 0 0 0-7-7zm0 9.5A2.5 2.5 0 1 1 12 6.5a2.5 2.5 0 0 1 0 5z"/></svg>
        Your Commercial or office address
      </li>
    </ul>

    <svg class="bands" viewBox="0 0 520 297" aria-hidden="true">
      <polygon class="bands__ink" points="330,231 520,184 520,200"/>
      <polygon class="bands__navy" points="0,286 520,200 520,297 0,297"/>
    </svg>
  </section>
</main>
</body>
</html>
```